Harrow Grading LLC business card design

Excavation company business cards

Contact Information for Business Card

Harrow Grading LLC cell phone 208-417-6290 office phone 208-319-4856 harrowgradingllc@maplecove.com Driveways, site prep, retaining walls, septic systems, rock delivery

Colors

Designer to choose colors to be used in the design.

```html
<!DOCTYPE html>
<html lang="en">
<head>
<meta charset="utf-8">
<title>Harrow Grading LLC – Business Card</title>
<link href="https://fonts.googleapis.com/css2?family=Montserrat:wght@400;500;800&display=swap" rel="stylesheet">
<style>
  :root {
    --stage: #2a2a2c;
    --orange: #e8681e;
    --card-dark: #161617;
    --ink: #1b1b1c;
    --grey-text: #a9a9ab;
    --steel-light: #8a8a8c;
    --steel-dark: #2e2e30;
  }
  * { margin: 0; padding: 0; box-sizing: border-box; }
  html, body {
    width: 1200px; height: 874px; overflow: hidden;
    background: var(--stage);
    font-family: "Montserrat", sans-serif;
  }
  .stage { position: relative; width: 1200px; height: 874px; }
  .card {
    position: absolute; left: 320px; width: 560px; height: 320px;
    border-radius: 22px; overflow: hidden;
  }
  .card-front {
    top: 72px; background: var(--orange);
    display: flex; align-items: center; justify-content: center;
  }
  .front-brand {
    display: flex; align-items: center; gap: 12px;
    color: var(--ink); font-weight: 800; font-size: 30px; letter-spacing: 1px;
    white-space: nowrap;
  }
  .brand-mark { width: 18px; height: 18px; background: currentColor; flex: none; }
  .card-back { top: 448px; background: var(--card-dark); color: var(--grey-text); }
  .back-brand {
    position: absolute; left: 34px; top: 40px;
    display: flex; align-items: center; gap: 10px;
    color: var(--orange); font-weight: 800; font-size: 22px; letter-spacing: .5px;
    white-space: nowrap;
  }
  .back-brand .brand-mark { width: 13px; height: 13px; }
  .holder { position: absolute; left: 34px; top: 96px; }
  .holder-name { color: var(--orange); font-weight: 800; font-size: 19px; letter-spacing: 1px; }
  .holder-role { font-size: 13px; margin-top: 2px; }
  .contact-list {
    position: absolute; left: 34px; top: 152px; list-style: none;
    font-size: 13.5px; font-weight: 500;
  }
  .contact-list li { display: flex; align-items: center; gap: 9px; height: 20px; }
  .contact-list svg { width: 12px; height: 12px; fill: var(--orange); flex: none; }
  .web-lines { position: absolute; left: 34px; top: 232px; font-size: 13.5px; font-weight: 500; }
  .web-lines .email { color: var(--grey-text); }
  .web-lines .site { color: var(--orange); margin-top: 4px; }
  .machine-art {
    position: absolute; right: 0; bottom: 0; width: 270px; height: 200px;
    background: radial-gradient(ellipse at 60% 65%, var(--steel-light) 0%, #555557 45%, var(--steel-dark) 80%, var(--card-dark) 100%);
  }
</style>
</head>
<body>
<main class="stage">
  <section class="card card-front">
    <div class="front-brand"><span class="brand-mark"></span>HARROW GRADING LLC</div>
  </section>

  <section class="card card-back">
    <div class="back-brand"><span class="brand-mark"></span>HARROW GRADING LLC</div>

    <div class="holder">
      <div class="holder-name">DANIEL REEVES</div>
      <div class="holder-role">President</div>
    </div>

    <ul class="contact-list">
      <li>
        <svg viewBox="0 0 24 24"><path d="M6.6 10.8a15.1 15.1 0 0 0 6.6 6.6l2.2-2.2a1 1 0 0 1 1-.25 11.4 11.4 0 0 0 3.6.57 1 1 0 0 1 1 1V20a1 1 0 0 1-1 1A17 17 0 0 1 3 4a1 1 0 0 1 1-1h3.5a1 1 0 0 1 1 1c0 1.25.2 2.45.57 3.57a1 1 0 0 1-.25 1z"/></svg>
        208-319-4856
      </li>
      <li>
        <svg viewBox="0 0 24 24"><path d="M7 1h10a2 2 0 0 1 2 2v18a2 2 0 0 1-2 2H7a2 2 0 0 1-2-2V3a2 2 0 0 1 2-2zm0 3v14h10V4zm5 15.5a1 1 0 1 0 0 2 1 1 0 0 0 0-2z"/></svg>
        208-417-6290
      </li>
      <li>
        <svg viewBox="0 0 24 24"><path d="M2 5h20v14H2zm2 2v.5l8 5 8-5V7zm0 2.8V17h16V9.8l-8 5z"/></svg>
        harrowgradingllc
      </li>
    </ul>

    <div class="web-lines">
      <div class="email">harrowgradingllc@maplecove.com</div>
      <div class="site">Harrowgradingllc.com</div>
    </div>

    <div class="machine-art" role="img" aria-label="Metallic illustration of an excavator in front of mountain peaks"></div>
  </section>
</main>
</body>
</html>
```